Home page design for Drone video business (the Business focusses on home videos for realtors)

Dear reader,

*I NEED DESIGNS OF ALL THE PAGES*
We need a first design of a homepage and of 4 other pages of the website of a business that sells drone video services. All the pages will need to be in the similar design style.
The video's are targeted at consumers that want to sell there home and would like to have a cool drone video of photos of their home.

How does the website look:
- has a navbar on top
- A cool looking banner of an areal drone.
- A Big header: with company name: SkyLoftReels
- A smaller subheader: We film your home to increase your chances of sale
- Then a section with a Big header: How does it work
- In this section a place for a vimeo explainitory video
- Then a similar navbar styled bar with a phone number and a email address
- Then a section where the videos porfolio is displayed in a cool way
- Inside this sectiona header: Our work

- A section with header: Why us?
- 4 symbols here with a subheader and some lorum ipsum text underneath (see wireframe images)

- Under that a: Contact us
- where you can put in name, email, phone, message box and a send button

- At the bottom a footer with phone number and a fake address for now.

Be creative. Use creative but serious color.
Use a serious font. Make it a sharp design. Sharp lines. Not to dark design and not to light design.

The wireframes are the same kind of images.
PLEASE PUT IN DESIGNS OF ALL THE PAGES

Good luck

Target Market(s)

People that want to sell home and want to make a cool drone video or photos of their home.

Industry/Entity Type

Business

Contact Information for Business Card

Lucas Wenning
lucas@skyloftreels.example
+31647208351

Logo Text

SkyLoftReels

Number of Pages Required

1 page

Font styles to use
Sans Serif

Requirements
Must have
• All the sections as explained in the instructions.
• The nav bar should have an about us, services, portfolio and a contact us buttons.
• See instruction for details.
• Must include designs of the front page, contact us, our services, portfolio and contact us.
• If you do add some designs for the "about us", "services", "prices", "portfolio" and "contact us" pages, you make a way better chance of winning the competition.
Nice to have
• designs for the other pages as described at the Must haves. You make a better chance of winning if you include them. Look at the wireframes to see the mockups for those pages. think creative about what kind of sections and design should be included in those pages.
Should not have
• bad designs.

```html
<!DOCTYPE html>
<html lang="en">
<head>
<meta charset="utf-8">
<title>SkyLoftReels – Home</title>
<link href="https://fonts.googleapis.com/css2?family=Open+Sans:wght@400;600;700;800&family=Roboto+Condensed:wght@700&display=swap" rel="stylesheet">
<style>
:root{
  --green:#76b82a;
  --green-dark:#4f7a2c;
  --slate:#464c55;
  --slate-deep:#3f444c;
  --slate-form:#4b5059;
  --footer:#2d3136;
  --footer-bar:#3a3e44;
  --white:#ffffff;
  --text-soft:#e9ecef;
  --input:#9ea3a9;
}
*{margin:0;padding:0;box-sizing:border-box}
html,body{width:1200px;height:3291px;overflow:hidden}
body{position:relative;font-family:"Open Sans",sans-serif;color:var(--white);background:var(--white)}
.abs{position:absolute}
.photo{position:absolute}

/* header */
.topbar{left:0;top:0;width:1200px;height:70px;background:rgba(40,44,50,.85);z-index:3}
.brand-tab{left:165px;top:0;width:157px;height:88px;background:var(--white);border-radius:0 0 14px 14px;z-index:4;display:flex;align-items:center;justify-content:center;box-shadow:0 2px 6px rgba(0,0,0,.3)}
.brand-tab span{font-weight:800;font-size:21px;color:var(--green)}
.nav{left:461px;top:20px;z-index:4;display:flex;gap:0}
.nav a{position:absolute;top:0;height:36px;line-height:36px;font-size:17px;font-weight:700;color:var(--white);text-decoration:none;white-space:nowrap}
.nav .active{background:var(--white);color:var(--green);border-radius:18px;width:88px;text-align:center}

/* hero */
.hero-photo{left:0;top:0;width:1200px;height:544px;background:linear-gradient(180deg,#6f9ccd 0%,#a9c7e6 30%,#3d6d98 45%,#2c5a80 70%,#6a7d5c 100%)}
.frame{border:2px solid rgba(255,255,255,.8)}
.frame-label{font-size:12px;font-weight:600;color:#fff}
.hero-title{left:0;width:1200px;top:262px;text-align:center;font-size:30px;font-weight:800;color:#3a3f45;letter-spacing:.5px}
.hero-sub{left:0;width:1200px;top:302px;text-align:center;font-size:17px;font-weight:800;color:#fff;line-height:22px}
.drone{left:362px;top:439px;width:494px;height:252px;background:radial-gradient(ellipse at center,#e5e6e8 0%,#9a9ea3 55%,rgba(255,255,255,0) 72%)}

/* how it works */
.how{left:0;top:698px;width:1200px;height:476px;background:var(--slate)}
.section-title{position:absolute;left:0;width:1200px;text-align:center;font-size:27px;font-weight:700;color:var(--white)}
.title-rule{position:absolute;left:540px;width:120px;height:4px;background:var(--green)}
.laptop{left:362px;top:801px;width:461px;height:280px;background:#f4f5f6;border-radius:16px 16px 0 0}
.laptop-base{left:308px;top:1081px;width:570px;height:14px;background:#f4f5f6;border-radius:0 0 10px 10px;border-top:2px solid #d5d8db}
.video{left:376px;top:816px;width:433px;height:250px;background:radial-gradient(ellipse at 60% 45%,#8a8f91,#4c5a3c 55%,#2b3a22)}
.play{width:58px;height:40px;background:#1a96c8;display:flex;align-items:center;justify-content:center}
.how-caption{left:0;width:1200px;top:1104px;text-align:center;font-size:15px;font-weight:700;line-height:20px}

/* contact strip */
.strip{left:0;width:1200px;background:var(--green)}
.icon-ring{width:59px;height:59px;border-radius:50%;background:var(--white);display:flex;align-items:center;justify-content:center}
.icon-ring i{width:49px;height:49px;border-radius:50%;background:var(--green);display:flex;align-items:center;justify-content:center}
.strip-text{font-size:33px;font-weight:700;color:var(--white);white-space:nowrap}
.strip-email{font-size:28px;font-weight:700}

/* our work */
.work{left:0;top:1273px;width:1200px;height:544px;background:var(--slate-deep)}
.intro{position:absolute;left:0;width:1200px;text-align:center;font-size:15px;font-weight:700;line-height:22px}
.arrow-panel{background:var(--green-dark);display:flex;align-items:center;justify-content:center}
.work-card{background:var(--green-dark);padding:7px;box-shadow:0 14px 22px rgba(0,0,0,.35)}
.work-card div{width:100%;height:100%;display:flex;align-items:center;justify-content:center}

/* why us */
.why{left:0;top:1817px;width:1200px;height:546px;background:linear-gradient(180deg,#6b7982 0%,#7c868a 40%,#6b6f62 75%,#5b5e4f 100%)}
.why-icon{width:48px;height:48px;background:var(--green);border-radius:6px;display:flex;align-items:center;justify-content:center}
.why-head{font-size:22px;font-weight:700;text-transform:uppercase}
.why-text{font-size:15px;font-weight:700;line-height:19px;width:360px}

/* call back */
.callback-photo{left:0;top:2363px;width:592px;height:481px;background:linear-gradient(160deg,#8a8e92 0%,#b0b3b6 45%,#6e7277 100%)}
.callback-form{left:592px;top:2363px;width:608px;height:481px;background:var(--slate-form)}
.callback-title{left:127px;top:2472px;font-family:"Roboto Condensed",sans-serif;font-size:46px;font-weight:700;color:var(--white);white-space:nowrap}
.form-intro{left:649px;top:2466px;width:420px;font-size:13px;line-height:22px;color:var(--text-soft)}
.label{font-size:11px;font-weight:700;text-transform:uppercase;color:var(--text-soft)}
.input{height:31px;background:var(--input);border:1px solid #c4c8cc;border-radius:3px}
.submit{left:649px;top:2697px;width:163px;height:48px;border-radius:24px;background:var(--green);font-size:21px;font-weight:700;display:flex;align-items:center;justify-content:center;letter-spacing:1px}

/* footer */
.footer{left:0;top:2947px;width:1200px;height:285px;background:var(--footer)}
.foot-head{font-size:22px;font-weight:700;text-transform:uppercase;white-space:nowrap}
.foot-rule{width:152px;height:4px;background:var(--green)}
.foot-about{left:136px;top:3064px;width:280px;font-size:17px;font-weight:700;line-height:31px}
.foot-links{left:483px;top:3068px;list-style:none}
.foot-links li{font-size:15px;font-weight:700;height:30.5px;text-transform:uppercase}
.foot-links li b{color:var(--green);margin-right:20px}
.news-input{left:788px;top:3074px;width:254px;height:44px;background:var(--white);font-size:14px;color:#8b8f94;padding:12px 20px}
.subscribe{left:790px;top:3142px;width:158px;height:37px;background:var(--green);font-size:18px;font-weight:700;display:flex;align-items:center;justify-content:center}
.bottom-bar{left:0;top:3232px;width:1200px;height:59px;background:var(--footer-bar)}
.copyright{left:136px;top:3250px;font-size:19px;font-weight:700}
.social{width:40px;height:40px;background:#25282c;display:flex;align-items:center;justify-content:center}
.social i{width:14px;height:14px;background:#d7d9dc;border-radius:2px}
.to-top{left:1139px;top:3210px;width:46px;height:46px;background:var(--green);display:flex;align-items:center;justify-content:center}
</style>
</head>
<body>

<!-- hero -->
<div class="photo hero-photo" role="img" aria-label="Aerial view of a coastline with beach, sea and cloudy sky"></div>
<div class="abs topbar"></div>
<div class="abs brand-tab"><span>SkyLoftReels</span></div>
<nav class="abs nav">
  <a class="active" style="left:0">HOME</a>
  <a style="left:107px">SERVICES</a>
  <a style="left:228px">ABOUT US</a>
  <a style="left:355px">PORTFOLIO</a>
  <a style="left:487px">CONTACT</a>
</nav>
<div class="abs frame" style="left:259px;top:103px;width:720px;height:406px"></div>
<div class="abs frame-label" style="left:266px;top:108px">4K 4096 x 2160</div>
<div class="abs frame" style="left:410px;top:191px;width:415px;height:279px"></div>
<div class="abs frame-label" style="left:418px;top:196px">HD 1920 X 1080</div>
<h1 class="abs hero-title">SKYLOFTREELS</h1>
<p class="abs hero-sub">WE FILM YOUR HOME TO INCREASE<br>YOUR CHANCES OF SALE</p>
<div class="photo drone" role="img" aria-label="White camera drone hovering with gimbal camera"></div>

<!-- how it works -->
<section class="abs how"></section>
<h2 class="section-title" style="top:741px">HOW DOES IT WORK</h2>
<div class="abs laptop"></div>
<div class="photo video" role="img" aria-label="Explainer video still of a drone in flight"></div>
<div class="abs play" style="left:559px;top:918px"><svg width="18" height="20" viewBox="0 0 18 20"><path d="M2 1 17 10 2 19Z" fill="#fff"/></svg></div>
<div class="abs laptop-base"></div>
<p class="abs how-caption">LOREM IPSUM DOLOR SIT AMET CONSECTETUER<br>ADIPISCING ELIT.</p>

<!-- contact strip -->
<div class="abs strip" style="top:1174px;height:99px"></div>
<div class="abs icon-ring" style="left:147px;top:1194px"><i><svg width="26" height="26" viewBox="0 0 24 24"><path d="M6.6 10.8a15 15 0 0 0 6.6 6.6l2.2-2.2c.3-.3.7-.4 1-.2 1.1.4 2.3.6 3.6.6.6 0 1 .4 1 1V20c0 .6-.4 1-1 1A17 17 0 0 1 3 4c0-.6.4-1 1-1h3.5c.6 0 1 .4 1 1 0 1.3.2 2.5.6 3.6.1.3 0 .7-.2 1Z" fill="#fff"/></svg></i></div>
<div class="abs strip-text" style="left:219px;top:1199px">+31682945163</div>
<div class="abs icon-ring" style="left:600px;top:1194px"><i><svg width="26" height="20" viewBox="0 0 26 20"><rect x="1" y="1" width="24" height="18" rx="2" fill="none" stroke="#fff" stroke-width="2"/><path d="M1 2l12 9 12-9" fill="none" stroke="#fff" stroke-width="2"/></svg></i></div>
<div class="abs strip-text strip-email" style="left:670px;top:1204px">contact@skyloftreels.example</div>

<!-- our work -->
<section class="abs work"></section>
<h2 class="section-title" style="top:1306px">OUR WORK</h2>
<div class="title-rule" style="top:1354px"></div>
<p class="intro" style="top:1380px">Lorem ipsum dolor sit amet consectetuer<br>adipiscing elit. Suspendisse et justo.</p>
<div class="abs arrow-panel" style="left:86px;top:1457px;width:48px;height:287px"><svg width="18" height="30" viewBox="0 0 18 30"><path d="M15 3 4 15l11 12" fill="none" stroke="#fff" stroke-width="5"/></svg></div>
<div class="abs work-card" style="left:143px;top:1457px;width:287px;height:287px"><div class="photo" style="position:static;background:linear-gradient(160deg,#9fb4c9,#6d6a5c 55%,#4a4336)" role="img" aria-label="Technician kneeling beside a drone on a runway"><span class="play"><svg width="18" height="20" viewBox="0 0 18 20"><path d="M2 1 17 10 2 19Z" fill="#fff"/></svg></span></div></div>
<div class="abs work-card" style="left:446px;top:1457px;width:287px;height:287px"><div class="photo" style="position:static;background:linear-gradient(170deg,#c4d4e2,#a8b9c8 55%,#5d6a70)" role="img" aria-label="Engineer in hard hat watching a drone near wind turbines"><span class="play"><svg width="18" height="20" viewBox="0 0 18 20"><path d="M2 1 17 10 2 19Z" fill="#fff"/></svg></span></div></div>
<div class="abs work-card" style="left:743px;top:1457px;width:318px;height:287px"><div class="photo" style="position:static;background:linear-gradient(170deg,#4f8fd8,#8bb7e6 50%,#8b5a3c)" role="img" aria-label="Engineer operating a drone with a tablet controller"><span class="play"><svg width="18" height="20" viewBox="0 0 18 20"><path d="M2 1 17 10 2 19Z" fill="#fff"/></svg></span></div></div>
<div class="abs arrow-panel" style="left:1071px;top:1460px;width:44px;height:284px"><svg width="18" height="30" viewBox="0 0 18 30"><path d="M3 3l11 12L3 27" fill="none" stroke="#fff" stroke-width="5"/></svg></div>

<!-- why us -->
<section class="photo why" role="img" aria-label="Drone flying over a misty hillside with a runner"></section>
<h2 class="section-title" style="top:1868px">WHY US</h2>
<p class="intro" style="top:1944px">Lorem ipsum dolor sit amet consectetuer<br>adipiscing elit. Suspendisse et justo.</p>

<div class="abs why-icon" style="left:136px;top:2008px"><svg width="28" height="26" viewBox="0 0 28 26"><rect x="3" y="1" width="22" height="24" rx="2" fill="none" stroke="#fff" stroke-width="2.5"/><path d="M8 8h12M8 13h12M8 18h12" stroke="#fff" stroke-width="2.5"/></svg></div>
<div class="abs why-head" style="left:197px;top:2016px">Cheap</div>
<p class="abs why-text" style="left:197px;top:2059px">Lorem ipsum dolor sit amet consectetuer adipiscing elit. Suspendisse et justo elit. Suspendisse et justo.</p>

<div class="abs why-icon" style="left:655px;top:2008px"><svg width="28" height="26" viewBox="0 0 28 26"><rect x="3" y="1" width="22" height="24" rx="2" fill="none" stroke="#fff" stroke-width="2.5"/><path d="M8 8h12M8 13h12M8 18h12" stroke="#fff" stroke-width="2.5"/></svg></div>
<div class="abs why-head" style="left:717px;top:2016px">Cheap</div>
<p class="abs why-text" style="left:717px;top:2059px">Lorem ipsum dolor sit amet consectetuer adipiscing elit. Suspendisse et justo elit. Suspendisse et justo.</p>

<div class="abs why-icon" style="left:136px;top:2180px"><svg width="28" height="26" viewBox="0 0 28 26"><rect x="3" y="1" width="22" height="24" rx="2" fill="none" stroke="#fff" stroke-width="2.5"/><path d="M8 8h12M8 13h12M8 18h12" stroke="#fff" stroke-width="2.5"/></svg></div>
<div class="abs why-head" style="left:197px;top:2188px">Cheap</div>
<p class="abs why-text" style="left:197px;top:2231px">Lorem ipsum dolor sit amet consectetuer adipiscing elit. Suspendisse et justo elit. Suspendisse et justo.</p>

<div class="abs why-icon" style="left:655px;top:2180px"><svg width="28" height="26" viewBox="0 0 28 26"><rect x="3" y="1" width="22" height="24" rx="2" fill="none" stroke="#fff" stroke-width="2.5"/><path d="M8 8h12M8 13h12M8 18h12" stroke="#fff" stroke-width="2.5"/></svg></div>
<div class="abs why-head" style="left:717px;top:2188px">Cheap</div>
<p class="abs why-text" style="left:717px;top:2231px">Lorem ipsum dolor sit amet consectetuer adipiscing elit. Suspendisse et justo elit. Suspendisse et justo.</p>

<!-- call back -->
<div class="photo callback-photo" role="img" aria-label="Group of business people standing in a concrete courtyard"></div>
<div class="abs callback-form"></div>
<h2 class="abs callback-title">REQUEST A CALL BACK</h2>
<p class="abs form-intro">Would you like to speak to one of our financial advisers over the phone? Just submit your details and we'll be in touch shortly. You can also e-mail us for any further concern.</p>
<div class="abs label" style="left:649px;top:2550px">Your Name</div>
<div class="abs label" style="left:869px;top:2550px">Your Email</div>
<div class="abs input" style="left:649px;top:2576px;width:191px"></div>
<div class="abs input" style="left:869px;top:2576px;width:195px"></div>
<div class="abs label" style="left:649px;top:2621px">I would like to discuss</div>
<div class="abs input" style="left:649px;top:2644px;width:415px"></div>
<div class="abs submit">SUBMIT</div>

<!-- footer band -->
<div class="abs strip" style="top:2844px;height:103px"></div>
<div class="abs icon-ring" style="left:136px;top:2863px;width:66px;height:66px"><i style="width:54px;height:54px"><svg width="28" height="28" viewBox="0 0 24 24"><path d="M6.6 10.8a15 15 0 0 0 6.6 6.6l2.2-2.2c.3-.3.7-.4 1-.2 1.1.4 2.3.6 3.6.6.6 0 1 .4 1 1V20c0 .6-.4 1-1 1A17 17 0 0 1 3 4c0-.6.4-1 1-1h3.5c.6 0 1 .4 1 1 0 1.3.2 2.5.6 3.6.1.3 0 .7-.2 1Z" fill="#fff"/></svg></i></div>
<div class="abs strip-text" style="left:224px;top:2870px;font-size:37px">+31682945163</div>
<div class="abs strip-text" style="left:823px;top:2873px;font-size:34px;font-weight:800">SkyLoftReels</div>

<!-- footer -->
<footer class="abs footer"></footer>
<div class="abs foot-head" style="left:136px;top:2993px">About Us</div>
<div class="abs foot-rule" style="left:136px;top:3039px;width:92px"></div>
<p class="abs foot-about">Lorem ipsum dolor sit consectetuer adipiscing. Suspendisse et justo. Suspendisse et justo.</p>
<div class="abs foot-head" style="left:483px;top:2993px">Usefull Links</div>
<div class="abs foot-rule" style="left:483px;top:3039px;width:118px"></div>
<ul class="abs foot-links">
  <li><b>&gt;</b>Home</li>
  <li><b>&gt;</b>Portfolio</li>
  <li><b>&gt;</b>Contact Us</li>
  <li><b>&gt;</b>Services</li>
</ul>
<div class="abs foot-head" style="left:788px;top:2996px">Newsletter</div>
<div class="abs foot-rule" style="left:788px;top:3042px;width:96px"></div>
<div class="abs news-input">Your email Address...</div>
<div class="abs subscribe">SUBSCRIBE</div>

<div class="abs bottom-bar"></div>
<div class="abs copyright">© SkyLoftReels 2016.</div>
<div class="abs social" style="left:840px;top:3241px"><i></i></div>
<div class="abs social" style="left:886px;top:3241px"><i></i></div>
<div class="abs social" style="left:932px;top:3241px"><i></i></div>
<div class="abs social" style="left:978px;top:3241px"><i></i></div>
<div class="abs social" style="left:1024px;top:3241px"><i></i></div>
<div class="abs to-top"><svg width="14" height="10" viewBox="0 0 14 10"><path d="M1 9 7 2l6 7Z" fill="#fff"/></svg></div>

</body>
</html>
```